Health and wellnes company needs business cards

We are a Health and wellness business just relocated to Spain. Here nobody knows our business so we would like to put some of our services on the card. Clean design with logo.

Contact Information for Business Card

Brightmeadow
Paula & Oskar Dunbeck
Calle del Almendro 57
Villamarenca del Sol
Mobile: 0046 731 402687
info@brightmeadow.example

Font styles to use
Serif

Colors
85cae6
85acd3
b768aa

Requirements
Must have
• these Services somewhere on the card
• - Private or group yoga
• - Reconnective healing
• - Kitesurfing lessons
• - Massage
• LOgo somewhere
Nice to have
• Colours that go with the logo please

```html
<!DOCTYPE html>
<html lang="en">
<head>
<meta charset="utf-8">
<title>Brightmeadow Business Card</title>
<link href="https://fonts.googleapis.com/css2?family=Montserrat:wght@400;700&family=Roboto+Condensed:wght@700&display=swap" rel="stylesheet">
<style>
  :root {
    --navy: #1d3d6e;
    --sky: #85cae6;
    --teal: #5fc3cc;
    --paper: #ffffff;
    --backdrop: #e6e8eb;
    --ink: #16243a;
  }
  * { box-sizing: border-box; margin: 0; padding: 0; }
  html, body { width: 1200px; height: 900px; overflow: hidden; }
  body {
    background: var(--backdrop);
    font-family: "Montserrat", sans-serif;
    position: relative;
  }
  .card {
    position: absolute;
    width: 560px;
    height: 320px;
    border-radius: 26px;
    background: var(--paper);
    overflow: hidden;
    box-shadow: 0 10px 30px rgba(0,0,0,0.18);
  }
  .card-front { left: 110px; top: 100px; }
  .card-back { left: 530px; top: 480px; }

  /* front */
  .brand {
    position: absolute;
    top: 62px; left: 0; right: 0;
    display: flex; align-items: center; justify-content: center; gap: 12px;
    color: var(--navy);
    font-weight: 700;
    font-size: 30px;
    letter-spacing: 1px;
    text-transform: uppercase;
  }
  .brand-dot {
    width: 34px; height: 34px; border-radius: 50%;
    background: var(--teal);
    flex: none;
  }
  .owners {
    position: absolute;
    top: 132px; left: 0; right: 0;
    text-align: center;
    color: var(--ink);
    font-weight: 700;
    font-size: 14px;
    line-height: 1.35;
    text-transform: uppercase;
  }
  .contact-band {
    position: absolute;
    left: 0; right: 0; bottom: 0;
    height: 70px;
    background: var(--navy);
    color: var(--paper);
    display: flex; align-items: center; justify-content: space-between;
    padding: 0 24px;
    font-size: 11px;
    letter-spacing: 0.3px;
  }
  .contact-item { display: flex; align-items: center; gap: 8px; line-height: 1.35; white-space: nowrap; }
  .contact-item svg { width: 14px; height: 14px; fill: var(--paper); flex: none; }

  /* back */
  .back-logo-side {
    position: absolute; left: 0; top: 0; bottom: 0; width: 270px;
    display: flex; align-items: center; justify-content: center; gap: 10px;
    color: var(--navy);
    font-weight: 700;
    font-size: 19px;
    text-transform: uppercase;
    letter-spacing: 1px;
  }
  .back-logo-side .brand-dot { width: 26px; height: 26px; }
  .services-panel {
    position: absolute; left: 270px; top: 0; bottom: 0; right: 0;
    background: var(--navy);
    border-left: 6px solid var(--sky);
    display: flex; flex-direction: column; justify-content: center; align-items: flex-end;
    gap: 18px;
    padding-right: 26px;
  }
  .service {
    font-family: "Roboto Condensed", sans-serif;
    font-weight: 700;
    color: var(--paper);
    font-size: 19px;
    text-transform: uppercase;
    letter-spacing: 0.5px;
    display: flex; align-items: center; gap: 14px;
  }
  .service::after {
    content: ""; width: 6px; height: 6px; border-radius: 50%; background: var(--paper);
  }
</style>
</head>
<body>
  <section class="card card-front">
    <div class="brand"><span class="brand-dot"></span>Brightmeadow</div>
    <p class="owners">Paula &amp;<br>Oskar Dunbeck</p>
    <div class="contact-band">
      <div class="contact-item">
        <svg viewBox="0 0 24 24" aria-hidden="true"><path d="M6.6 10.8a15 15 0 0 0 6.6 6.6l2.2-2.2a1 1 0 0 1 1-.25 11.4 11.4 0 0 0 3.6.57 1 1 0 0 1 1 1V20a1 1 0 0 1-1 1A17 17 0 0 1 3 4a1 1 0 0 1 1-1h3.5a1 1 0 0 1 1 1c0 1.25.2 2.450.57 3.57a1 1 0 0 1-.25 1z"/></svg>
        <span>0046 731 402687</span>
      </div>
      <div class="contact-item">
        <svg viewBox="0 0 24 24" aria-hidden="true"><path d="M12 2a7 7 0 0 0-7 7c0 5.2 7 13 7 13s7-7.8 7-13a7 7 0 0 0-7-7zm0 9.5A2.5 2.5 0 1 1 12 6.5a2.5 2.5 0 0 1 0 5z"/></svg>
        <span>Calle del Almendro 57<br>Villamarenca del Sol</span>
      </div>
      <div class="contact-item">
        <svg viewBox="0 0 24 24" aria-hidden="true"><path d="M3 5h18a1 1 0 0 1 1 1v12a1 1 0 0 1-1 1H3a1 1 0 0 1-1-1V6a1 1 0 0 1 1-1zm9 7.2L4 7v1.9l8 5.1 8-5.1V7z"/></svg>
        <span>info@brightmeadow.example</span>
      </div>
    </div>
  </section>

  <section class="card card-back">
    <div class="back-logo-side"><span class="brand-dot"></span>Brightmeadow</div>
    <div class="services-panel">
      <p class="service">Massage</p>
      <p class="service">Kitesurfing Lessons</p>
      <p class="service">Reconnective Healing</p>
      <p class="service">Private or Group Yoga</p>
    </div>
  </section>
</body>
</html>
```